U.S. Popcorn company needs business cards

We are a popcorn company that manufactures popcorn and sells it to grocery stores worldwide. Our theme is "Americana" and our logo is U.S. route 66 which is the most famous highway in the U.S.

We would like the design to be simple and to use both sides. On the back side we would like to see just the logo and website. The front would be normal details

Target Market(s)

Wholesalers, grocers and distributors

Industry/Entity Type

Manufacture

Contact Information for Business Card

Business name: Prairie Lantern Popcorn
Phone: +1 555 308 4726
Email: Dale@prairielanternpopcorn.com
website: www.prairielanternpopcorn.com
Tag Line: "Fresh-popped every day"
Name: Dale Whitcombe
Title: Founder/President

Requirements
Must have
• Either this design should be fun or clean and simple. I will let you show me your thougths.
Nice to have
• Anything that ties in the real Hwy Route 66.
• Colors might need to be red, white and blue incorporated.
Should not have
• Not be too busy.

```html
<!DOCTYPE html>
<html lang="en">
<head>
<meta charset="utf-8">
<title>Prairie Lantern Popcorn – Business Cards</title>
<link rel="stylesheet" href="https://fonts.googleapis.com/css2?family=Poppins:wght@400;600;700&display=swap">
<style>
  :root {
    --navy: #13306b;
    --red: #d8222a;
    --white: #ffffff;
    --paper: #ececec;
    --card-edge: #d9d9d9;
    --ink-soft: #e9edf5;
  }
  * { margin: 0; padding: 0; box-sizing: border-box; }
  html, body { width: 1200px; height: 576px; overflow: hidden; }
  body {
    background: var(--paper);
    font-family: "Poppins", "Century Gothic", sans-serif;
    position: relative;
  }
  .card {
    position: absolute;
    top: 139px;
    width: 484px;
    height: 293px;
    border-radius: 6px;
    overflow: hidden;
    background: var(--white);
    border: 1px solid var(--card-edge);
  }
  .card--back { left: 80px; }
  .card--front { left: 601px; }

  /* Back */
  .brand-mark {
    position: absolute;
    left: 0; right: 0; top: 104px;
    display: flex; align-items: center; justify-content: center; gap: 12px;
  }
  .brand-mark__dot {
    width: 22px; height: 22px; border-radius: 50%; background: var(--navy);
  }
  .brand-mark__name {
    color: var(--navy); font-weight: 700; font-size: 26px; line-height: 1.1;
  }
  .back-web {
    position: absolute; left: 0; right: 0; top: 256px;
    display: flex; align-items: center; justify-content: center; gap: 12px;
    color: var(--navy); font-weight: 600; font-size: 11px;
  }
  .back-web__domain { color: var(--red); }
  .back-web__rule { width: 56px; height: 2px; background: var(--navy); border-radius: 1px; }

  /* Front */
  .front-bg { position: absolute; inset: 0; }
  .person { position: absolute; left: 22px; top: 34px; color: var(--white); }
  .person__name { font-weight: 600; font-size: 22px; line-height: 1.1; }
  .person__title { font-size: 11px; margin-top: 2px; }
  .front-brand {
    position: absolute; left: 300px; top: 74px; width: 170px;
    display: flex; align-items: center; gap: 8px;
  }
  .front-brand__dot { width: 14px; height: 14px; border-radius: 50%; background: var(--navy); flex: none; }
  .front-brand__name { color: var(--navy); font-weight: 700; font-size: 16px; line-height: 1.15; }
  .contacts {
    position: absolute; left: 22px; top: 214px; list-style: none;
    color: var(--ink-soft); font-size: 12.5px;
  }
  .contacts li { display: flex; align-items: center; gap: 12px; height: 17px; }
  .contacts svg { width: 11px; height: 11px; flex: none; }
  .tagline {
    position: absolute; right: 22px; top: 245px;
    color: var(--white); font-size: 14px;
  }
</style>
</head>
<body>

<section class="card card--back" aria-label="Card back">
  <div class="brand-mark">
    <span class="brand-mark__dot"></span>
    <span class="brand-mark__name">Prairie Lantern<br>Popcorn</span>
  </div>
  <div class="back-web">
    <span class="back-web__rule"></span>
    <span>www.<span class="back-web__domain">prairielanternpopcorn</span>.com</span>
    <span class="back-web__rule"></span>
  </div>
</section>

<section class="card card--front" aria-label="Card front">
  <svg class="front-bg" width="484" height="293" viewBox="0 0 484 293" aria-hidden="true">
    <rect width="484" height="293" fill="var(--navy)"/>
    <path d="M174 0 C236 0 250 95 300 152 C340 196 400 204 484 204 L484 0 Z" fill="var(--red)"/>
    <path d="M200 0 C254 0 266 92 316 146 C356 190 412 200 484 206 L484 0 Z" fill="var(--white)"/>
  </svg>

  <div class="person">
    <div class="person__name">Dale Whitcombe</div>
    <div class="person__title">Founder/President</div>
  </div>

  <div class="front-brand">
    <span class="front-brand__dot"></span>
    <span class="front-brand__name">Prairie Lantern Popcorn</span>
  </div>

  <ul class="contacts">
    <li>
      <svg viewBox="0 0 12 12" aria-hidden="true"><path d="M1 4 Q6 0 11 4 L9.5 5.5 L8 4.5 L4 4.5 L2.5 5.5 Z M3 6 H9 L10 11 H2 Z" fill="var(--ink-soft)"/></svg>
      <span>+1 555 308 4726</span>
    </li>
    <li>
      <svg viewBox="0 0 12 12" aria-hidden="true"><rect x="0.5" y="2" width="11" height="8" fill="none" stroke="var(--ink-soft)"/><path d="M0.5 2 L6 6.5 L11.5 2" fill="none" stroke="var(--ink-soft)"/></svg>
      <span>Dale@prairielanternpopcorn.com</span>
    </li>
    <li>
      <svg viewBox="0 0 12 12" aria-hidden="true"><circle cx="6" cy="6" r="5.2" fill="none" stroke="var(--ink-soft)"/><ellipse cx="6" cy="6" rx="2.2" ry="5.2" fill="none" stroke="var(--ink-soft)"/><path d="M0.8 6 H11.2" stroke="var(--ink-soft)"/></svg>
      <span>prairielanternpopcorn.com</span>
    </li>
  </ul>

  <p class="tagline">"Fresh-popped every day"</p>
</section>

</body>
</html>
```